Business Card Design Project

I need a business card designed from scratch. I have an existing logo that I can upload in Illustrator for modification or redesign.

The Company is called Query Lanterns http://querylanterns.com.au and we provide Search Engine Optimization services to Australian businesses. The current logo signifies an increase in visitors, profits etc...

There are no restrictions as to the redesign - colours, style etc are all open to change.

Cards will be full colour and one sided printed at http://www.cardmoxel.com.au so check their requirements for file format and sizes etc.

I will expect all original files upon completion of project.

Target Market(s)

Any business with a web site looking to improve their search engine rankings

Industry/Entity Type

Business

Requirements
Must have
• I like modern, sleek designs. Clean, not fussy, uncluttered.

```html
<!DOCTYPE html>
<html lang="en">
<head>
<meta charset="utf-8">
<title>Query Lanterns – Business Card</title>
<link href="https://fonts.googleapis.com/css2?family=Open+Sans:wght@400;600;700;800&display=swap" rel="stylesheet">
<style>
  :root {
    --backdrop: #e9e6e2;
    --card: #ffffff;
    --brand-blue: #1a72b9;
    --brand-blue-light: #3b8fd0;
    --brand-blue-dark: #135a96;
    --accent-yellow: #f5c400;
    --ink: #3d3d3d;
  }
  * { box-sizing: border-box; margin: 0; padding: 0; }
  html, body {
    width: 1200px; height: 460px; overflow: hidden;
    background: var(--backdrop);
    font-family: "Open Sans", Arial, sans-serif;
  }
  .card {
    position: absolute; top: 76px;
    width: 542px; height: 308px;
    background: var(--card);
    border-radius: 16px;
    box-shadow: 0 3px 8px rgba(0,0,0,.18);
    overflow: hidden;
  }
  .card--front { left: 47px; }
  .card--back { left: 612px; }

  .brand {
    position: absolute; top: 72px; left: 0; right: 0;
    display: flex; align-items: center; justify-content: center; gap: 14px;
  }
  .brand__dot {
    width: 26px; height: 26px; border-radius: 50%;
    background: var(--accent-yellow);
  }
  .brand__name {
    font-weight: 800; font-size: 40px; letter-spacing: -0.5px;
    color: var(--brand-blue);
  }

  .band {
    position: absolute; top: 192px; left: 0;
    width: 500px; height: 33px;
    background: linear-gradient(180deg, var(--brand-blue-light) 0%, var(--brand-blue) 55%, var(--brand-blue-dark) 100%);
    display: flex; align-items: center; justify-content: center;
    color: #fff;
  }
  .band__tab {
    position: absolute; top: 192px; left: 506px;
    width: 36px; height: 33px;
    background: var(--accent-yellow);
  }
  .band__name { font-weight: 700; font-size: 16px; }
  .band__title { font-size: 13px; margin-left: 6px; }
  .band__web { font-size: 13px; letter-spacing: 2.6px; }

  .contacts {
    position: absolute; top: 243px; left: 25px; right: 10px;
    display: flex; gap: 18px;
    font-size: 13px; line-height: 19px; color: var(--ink);
  }
  .contacts__col p { display: flex; align-items: center; gap: 5px; white-space: nowrap; }
  .contacts__col svg { width: 10px; height: 10px; fill: var(--brand-blue); flex: none; }
</style>
</head>
<body>

<section class="card card--front">
  <div class="brand">
    <span class="brand__dot"></span>
    <span class="brand__name">Query Lanterns</span>
  </div>
  <div class="band">
    <span class="band__name">Your Name</span><span class="band__title">Title</span>
  </div>
  <div class="band__tab"></div>
  <div class="contacts">
    <div class="contacts__col">
      <p>00Floor Street, City Name</p>
      <p>State Name, Contry Name</p>
    </div>
    <div class="contacts__col">
      <p><svg viewBox="0 0 10 10"><path d="M2 0h2l1 3-1.5 1a6 6 0 0 0 2.5 2.5L7 5l3 1v2a2 2 0 0 1-2 2A8 8 0 0 1 0 2a2 2 0 0 1 2-2z"/></svg>098 765 4321</p>
      <p><svg viewBox="0 0 10 10"><rect x="2" y="0" width="6" height="10" rx="1"/><rect x="3" y="1.5" width="4" height="5" fill="#fff"/></svg>098 765 4321</p>
    </div>
    <div class="contacts__col">
      <p><svg viewBox="0 0 10 10"><rect x="0" y="2" width="10" height="6.5" rx="1"/><path d="M0.5 2.5L5 6l4.5-3.5" stroke="#fff" fill="none"/></svg>enquiry@querylanterns.com.au</p>
      <p><svg viewBox="0 0 10 10"><circle cx="5" cy="5" r="5"/><path d="M0 5h10M5 0c-2 3-2 7 0 10M5 0c2 3 2 7 0 10" stroke="#fff" stroke-width=".7" fill="none"/></svg>www.querylanterns.com.au</p>
    </div>
  </div>
</section>

<section class="card card--back">
  <div class="brand">
    <span class="brand__dot"></span>
    <span class="brand__name">Query Lanterns</span>
  </div>
  <div class="band">
    <span class="band__web">www.querylanterns.com.au</span>
  </div>
  <div class="band__tab"></div>
</section>

</body>
</html>
```